Business card design needed

I run a Beautician studio (for 7 years now)
I offer
- Velmo Body Sugaring
- Ruby Glaze
- Nails
- Facials
- Manicure
- Foot Treatment
It might not be necessary to list all those treatments?
Maybe the link to the Website is sufficient?
I leave that up to you ...
(more info on www.FernAndDewByLenka.com.au)
Velmo BodySugaring is our biggest success, It replaces waxing.
I would like to incorporate the logo into the Business Card.
We had many complaints regarding our old Business Cards as the Phone Number was to small.
On the backside, we would like a "your next Appointment" section.
Looking forward to you Design, cheers ... Lenka
Industry/Entity Type
Business
Contact Information for Business Card
Fern by Dew by Lenka
14 Korrin Sqr 3942 Berwick
www.FernAndDewByLenka.com.au
03 9481 2267

```html
<!DOCTYPE html>
<html lang="en">
<head>
<meta charset="utf-8">
<title>Fern by Dew by Lenka – Business Cards</title>
<link href="https://fonts.googleapis.com/css2?family=Arimo:wght@400;700&family=Cinzel:wght@500&family=Open+Sans:wght@400;600;700&display=swap" rel="stylesheet">
<style>
  :root{
    --backdrop:#1c1c1c;
    --card:#ffffff;
    --green:#1f9a4a;
    --green-dark:#1d6b35;
    --orange:#e8602a;
    --yellow:#f5c21f;
    --ink:#2a2a2a;
    --grey:#555555;
    --rule:#9a9a9a;
    --brand-dot:#f29a26;
  }
  *{box-sizing:border-box;margin:0;padding:0}
  html,body{width:1200px;height:728px;overflow:hidden;background:var(--backdrop)}
  .sheet{position:relative;width:1200px;height:728px}
  .card{position:absolute;width:542px;height:308px;background:var(--card);overflow:hidden;font-family:"Arimo",Arial,sans-serif;color:var(--ink)}
  .card--front{left:41px;top:36px}
  .card--appt{left:615px;top:37px}
  .card--back{left:41px;top:380px}
  .card--appt-alt{left:625px;top:384px}

  /* brand name lockup */
  .brand{position:absolute;display:flex;flex-direction:column;align-items:center;gap:10px}
  .brand__dot{width:22px;height:22px;border-radius:50%;background:var(--brand-dot)}
  .brand__name{font-family:"Open Sans",sans-serif;font-weight:600;color:var(--ink);letter-spacing:.18em;text-transform:uppercase;text-align:center;line-height:1.25}

  /* front */
  .front__title{position:absolute;top:22px;left:0;width:100%;text-align:center;font-weight:700;font-size:24px;letter-spacing:.07em;color:var(--green)}
  .treatments{position:absolute;left:65px;top:88px}
  .treatments__head{font-weight:700;font-size:16.5px;letter-spacing:.04em;color:var(--green);margin-bottom:4px}
  .treatments__list{list-style:none;font-size:14.5px;line-height:21px;color:var(--ink)}
  .front__divider{position:absolute;left:271px;top:86px;width:2px;height:120px;background:linear-gradient(var(--card),var(--rule),var(--card))}
  .card--front .brand{left:300px;top:112px;width:200px}
  .card--front .brand__name{font-size:17px}
  .front__wave{position:absolute;left:0;bottom:0;width:542px;height:90px}
  .front__contact{position:absolute;left:0;bottom:10px;width:100%;display:flex;justify-content:center;gap:22px;font-size:16px;color:var(--ink)}
  .front__contact span{display:flex;align-items:center;gap:6px}
  .front__contact svg{width:15px;height:15px}

  /* appointment */
  .appt__title{position:absolute;left:36px;top:55px;font-family:"Cinzel",serif;font-weight:500;font-size:18px;color:var(--green-dark)}
  .appt__row{position:absolute;left:36px;display:flex;align-items:flex-end;font-size:14.5px;color:var(--ink)}
  .appt__row--name{top:92px}
  .appt__row--date{top:130px}
  .appt__row--next{top:167px}
  .appt__line{display:inline-block;border-bottom:1px dotted var(--grey);height:1px;margin:0 6px 5px}
  .appt__line--solid{border-bottom-style:solid}
  .appt__box{display:inline-block;width:97px;height:20px;border:1px solid var(--grey);margin-left:10px}
  .appt__box + .appt__box{margin-left:30px}
  .appt__days{position:absolute;left:33px;top:203px;display:flex;align-items:center;font-weight:700;font-size:14.5px;color:var(--grey)}
  .appt__days span{margin-right:7px}
  .appt__days i{display:inline-block;width:34px;height:20px;border:1px solid var(--grey);margin-right:8px}
  .appt__note{position:absolute;left:33px;top:251px;width:480px;font-size:12.5px;line-height:18px;color:var(--ink)}
  .card--appt .brand{right:52px;top:24px;gap:6px}
  .card--appt .brand__dot{width:16px;height:16px}
  .card--appt .brand__name{font-size:11px}
  .appt__watermark{position:absolute;left:120px;top:190px;width:340px;text-align:center;font-family:"Open Sans",sans-serif;font-weight:600;font-size:34px;letter-spacing:.18em;color:#f1f1f1;text-transform:uppercase}

  /* back */
  .card--back .brand{left:0;top:58px;width:100%}
  .card--back .brand__dot{width:32px;height:32px}
  .card--back .brand__name{font-size:24px}
  .back__url{position:absolute;top:200px;width:100%;text-align:center;font-family:"Open Sans",sans-serif;font-size:13.5px;letter-spacing:.12em;color:var(--ink)}
  .back__hours-head{position:absolute;top:232px;width:100%;text-align:center;font-family:"Open Sans",sans-serif;font-weight:600;font-size:19px;letter-spacing:.07em;color:var(--grey)}
  .back__hours{position:absolute;top:268px;width:100%;text-align:center;font-family:"Open Sans",sans-serif;font-weight:600;font-size:14.5px;color:var(--grey)}
  .back__hours em{font-style:normal;color:#bbb;margin:0 6px}
</style>
</head>
<body>
<main class="sheet">

  <section class="card card--front">
    <h1 class="front__title">FERN BY DEW BY LENKA</h1>
    <div class="treatments">
      <p class="treatments__head">Treatments offer</p>
      <ul class="treatments__list">
        <li>• Velmo Body Sugaring</li>
        <li>• Ruby Glaze • Nails</li>
        <li>• Facials • Manicure</li>
        <li>• Foot Treatment</li>
      </ul>
    </div>
    <div class="front__divider"></div>
    <div class="brand">
      <span class="brand__dot"></span>
      <span class="brand__name">Velmo<br>Body Sugaring</span>
    </div>
    <svg class="front__wave" viewBox="0 0 542 90" preserveAspectRatio="none">
      <defs>
        <linearGradient id="bandGrad" x1="0" x2="1" y1="0" y2="0">
          <stop offset="0" stop-color="#e8602a"/>
          <stop offset="1" stop-color="#f5c21f"/>
        </linearGradient>
      </defs>
      <path d="M0 12 C120 45 220 45 330 22 C420 4 490 0 542 2 L542 90 L0 90 Z" fill="url(#bandGrad)"/>
      <path d="M0 8 C120 40 220 40 330 17 C420 0 490 -4 542 -2 L542 4 C490 3 420 8 330 26 C220 48 120 48 0 16 Z" fill="#1f9a4a"/>
    </svg>
    <div class="front__contact">
      <span><svg viewBox="0 0 16 16"><circle cx="8" cy="8" r="7" fill="none" stroke="#2a2a2a" stroke-width="1.4"/><path d="M5.2 4.5l1.6-.3.8 2-1 .8a5 5 0 0 0 2.4 2.4l.8-1 2 .8-.3 1.6c-3.5.2-6.5-2.8-6.3-6.3z" fill="#2a2a2a"/></svg>03 9481 2267</span>
      <span><svg viewBox="0 0 16 16"><circle cx="8" cy="8" r="7.5" fill="#2a2a2a"/><path d="M8 3.5a3 3 0 0 0-3 3c0 2.2 3 6 3 6s3-3.8 3-6a3 3 0 0 0-3-3zm0 4.2a1.2 1.2 0 1 1 0-2.4 1.2 1.2 0 0 1 0 2.4z" fill="#fff"/></svg>14 Korrin Sqr 3942 Berwick</span>
    </div>
  </section>

  <section class="card card--appt">
    <div class="brand">
      <span class="brand__dot"></span>
      <span class="brand__name">Velmo<br>Body Sugaring</span>
    </div>
    <h2 class="appt__title">YOUR APPOINTMENT</h2>
    <p class="appt__row appt__row--name">Name :<span class="appt__line" style="width:290px"></span></p>
    <p class="appt__row appt__row--date">Date :<span class="appt__line appt__line--solid" style="width:95px;margin-left:20px"></span>Time :<span class="appt__line" style="width:90px"></span>am / pm</p>
    <p class="appt__row appt__row--next">Next Appointment<span class="appt__box"></span><span class="appt__box"></span></p>
    <p class="appt__days"><span>MON</span><i></i><span>TUE</span><i></i><span>WED</span><i></i><span>THU</span><i></i><span>FRI</span><i></i><span>SAT</span><i></i></p>
    <p class="appt__note">It would be appreciated if 24 hours notice could be given if you are unable to attend an appointment</p>
  </section>

  <section class="card card--back">
    <div class="brand">
      <span class="brand__dot"></span>
      <span class="brand__name">Velmo<br>Body Sugaring</span>
    </div>
    <p class="back__url">www.FernAndDewByLenka.com.au</p>
    <h2 class="back__hours-head">Hours of Operation</h2>
    <p class="back__hours">Mon - Fri: 7.30am - 7.00pm<em>|</em>Saturday: 7.30am - 12.00pm</p>
  </section>

  <section class="card card--appt-alt">
    <p class="appt__watermark" aria-hidden="true">Velmo</p>
    <h2 class="appt__title">YOUR APPOINTMENT</h2>
    <p class="appt__row appt__row--name">Name :<span class="appt__line" style="width:290px"></span></p>
    <p class="appt__row appt__row--date">Date :<span class="appt__line appt__line--solid" style="width:95px;margin-left:20px"></span>Time :<span class="appt__line" style="width:90px"></span>am / pm</p>
    <p class="appt__row appt__row--next">Next Appointment<span class="appt__box"></span><span class="appt__box"></span></p>
    <p class="appt__days"><span>MON</span><i></i><span>TUE</span><i></i><span>WED</span><i></i><span>THU</span><i></i><span>FRI</span><i></i><span>SAT</span><i></i></p>
    <p class="appt__note">It would be appreciated if 24 hours notice could be given if you are unable to attend an appointment</p>
  </section>

</main>
</body>
</html>
```